Design a compelling Tarnwove Business Card that will drive people to my site

I want a business card that I can give to people—less to tell them who I am and more to direct them to my website. My website is a portal for Pelmor Aquatics Officials and a place for people who want to become Pelmor Aquatics Officials.
I am uploading my official company logo as well as a business card mockup that I did on my own. Please feel free to completely stray from this design.
I've included a screen recording of the homepage of my website as well.
Target Market(s)
Pelmor Aquatics Officials and people who desire to become one
Contact Information for Business Card
website url
Look and feel
Each slider illustrates characteristics of the customer's brand and the style your logo design should communicate.

```html
<!DOCTYPE html>
<html lang="en">
<head>
<meta charset="utf-8">
<title>Tarnwove Business Card</title>
<link href="https://fonts.googleapis.com/css2?family=Montserrat:wght@400;500;700&display=swap" rel="stylesheet">
<style>
  :root {
    --stage: #3b3b3d;
    --brand-blue: #3a55a8;
    --brand-blue-soft: #4563b5;
    --brand-light: #93a6d8;
    --paper: #ffffff;
    --ink-white: #ffffff;
  }
  * { margin: 0; padding: 0; box-sizing: border-box; }
  html, body {
    width: 1200px; height: 915px; overflow: hidden;
    background: var(--stage);
    font-family: "Montserrat", sans-serif;
  }
  .stage { position: relative; width: 1200px; height: 915px; }
  .card {
    position: absolute;
    width: 620px; height: 354px;
    border-radius: 22px;
    overflow: hidden;
  }
  /* Front */
  .card-front {
    left: 90px; top: 90px;
    background: radial-gradient(circle at 60% 40%, var(--brand-blue-soft), var(--brand-blue) 70%);
    display: flex; align-items: center; justify-content: center;
  }
  .brand-lockup { display: flex; align-items: center; gap: 16px; }
  .brand-dot {
    width: 34px; height: 34px; border-radius: 50%;
  }
  .card-front .brand-dot { background: var(--ink-white); }
  .card-front .brand-name {
    font-weight: 700; font-size: 82px; letter-spacing: -2px;
    color: var(--ink-white); line-height: 1;
  }
  /* Back */
  .card-back {
    left: 490px; top: 470px;
    background: var(--paper);
  }
  .back-band { position: absolute; inset: 0; }
  .card-back .brand-lockup { position: absolute; left: 36px; top: 70px; }
  .card-back .brand-dot { background: var(--brand-blue); width: 26px; height: 26px; }
  .card-back .brand-name {
    font-weight: 700; font-size: 60px; letter-spacing: -1.5px;
    color: var(--brand-blue); line-height: 1;
  }
  .contact-block {
    position: absolute; left: 44px; top: 206px;
    color: var(--ink-white);
  }
  .person-name { font-weight: 700; font-size: 21px; color: var(--brand-light); }
  .person-title { font-size: 14px; margin-top: 2px; }
  .divider { width: 22px; height: 1px; background: var(--brand-light); margin: 10px 0 8px; }
  .contact-list { list-style: none; }
  .contact-list li {
    display: flex; align-items: center; gap: 8px;
    font-size: 14px; line-height: 22px;
  }
  .contact-list svg { width: 13px; height: 13px; fill: var(--brand-light); flex: none; }
</style>
</head>
<body>
<main class="stage">
  <section class="card card-front" role="img" aria-label="Blue card front with soft floating bubble pattern behind the Tarnwove name">
    <div class="brand-lockup">
      <span class="brand-dot"></span>
      <span class="brand-name">Tarnwove</span>
    </div>
  </section>

  <section class="card card-back">
    <svg class="back-band" viewBox="0 0 620 354" preserveAspectRatio="none" aria-hidden="true">
      <path d="M0 200 L360 200 C420 200 440 240 500 200 C540 170 580 120 620 108 L620 354 L0 354 Z" fill="var(--brand-blue)"/>
    </svg>
    <div class="brand-lockup">
      <span class="brand-dot"></span>
      <span class="brand-name">Tarnwove</span>
    </div>
    <div class="contact-block">
      <p class="person-name">Marcus Ellery</p>
      <p class="person-title">CEO &amp; Founder</p>
      <div class="divider"></div>
      <ul class="contact-list">
        <li>
          <svg viewBox="0 0 24 24"><path d="M6.6 10.8a15.1 15.1 0 0 0 6.6 6.6l2.2-2.2c.3-.3.7-.4 1-.2 1.1.4 2.3.6 3.6.6.6 0 1 .4 1 1V20c0 .6-.4 1-1 1A17 17 0 0 1 3 4c0-.6.4-1 1-1h3.5c.6 0 1 .4 1 1 0 1.3.2 2.5.6 3.6.1.3 0 .7-.2 1z"/></svg>
          (555) 201-4837
        </li>
        <li>
          <svg viewBox="0 0 24 24"><path d="M2 5h20v14H2z M2 5l10 8 10-8" /></svg>
          marcus@tarnwove.com
        </li>
        <li>
          <svg viewBox="0 0 24 24"><circle cx="12" cy="12" r="10"/></svg>
          www.tarnwove.com
        </li>
      </ul>
    </div>
  </section>
</main>
</body>
</html>
```